Redesign of LumoWordfind.com in Bootstrap 4

Current design of LumoWordfind.com is not responsive. We need to change it to latest version of Bootstrap 4 keeping essential elements in place.

Apart from home page, we need designs for http://www.lumowordfind.com/meaning/cat also.

Coding

Number of Pages Required

2 page

Colors
34a7d8

Requirements
Must have
• Bootstrap 4

```html
<!DOCTYPE html>
<html lang="en">
<head>
<meta charset="utf-8">
<title>Lumo Wordfind – English Dictionary</title>
<link href="https://fonts.googleapis.com/css2?family=Open+Sans:wght@400;600;700&family=Signika:wght@600;700&display=swap" rel="stylesheet">
<style>
:root{
  --blue:#34a7d8;
  --blue-dark:#2592c2;
  --orange:#f7941d;
  --orange-deep:#ff8a00;
  --teal-1:#46b3c9;
  --teal-2:#2f93b0;
  --ink:#333;
  --muted:#555;
  --line:#dcdcdc;
  --panel:#e6e6e6;
  --page:#ededed;
}
*{box-sizing:border-box;margin:0;padding:0}
html,body{width:982px;height:1200px;overflow:hidden}
body{font-family:"Open Sans",Arial,sans-serif;color:var(--ink);background:var(--page);position:relative}
.abs{position:absolute}

/* header */
.hero{left:0;top:0;width:982px;height:338px;background:radial-gradient(ellipse at 55% 45%,var(--teal-1),var(--teal-2) 85%)}
.menu{left:133px;top:16px;display:flex;align-items:center;gap:11px;color:#fff;font-size:10px;font-weight:700;letter-spacing:.5px}
.menu span.bars{display:block;width:21px;height:17px;border-top:2px solid #fff;border-bottom:2px solid #fff;position:relative}
.menu span.bars::after{content:"";position:absolute;left:0;right:0;top:5.5px;border-top:2px solid #fff}
.brand{left:427px;top:0;width:86px;height:62px;background:#a8dbe8;display:flex;flex-direction:column;align-items:center;justify-content:center;color:var(--blue-dark)}
.brand b{font-family:"Signika",sans-serif;font-size:17px;line-height:1}
.brand small{font-size:8px;letter-spacing:.5px;margin-top:3px}
.signin{left:794px;top:14px;width:57px;height:27px;border:2px solid var(--orange);color:var(--orange);font-size:9.5px;font-weight:700;display:flex;align-items:center;justify-content:center;letter-spacing:.5px}
.join{left:950px;top:116px;width:32px;height:116px;background:var(--orange);color:#fff;font-family:"Signika",sans-serif;font-size:11px;font-weight:700;writing-mode:vertical-rl;transform:rotate(180deg);display:flex;align-items:center;justify-content:center;letter-spacing:.5px}
.hero-title{left:0;width:982px;top:160px;text-align:center;color:#fff;font-weight:400;font-size:29px;line-height:40px;text-shadow:0 1px 3px rgba(0,0,0,.2)}
.search{left:273px;top:218px;width:436px;height:43px;background:rgba(255,255,255,.35);padding:3px;display:flex}
.search .field{flex:1;background:#fff;display:flex;align-items:center;padding-left:16px;font-size:12.5px;color:#444}
.search .go{width:83px;background:var(--orange);color:#fff;font-family:"Signika",sans-serif;font-weight:700;font-size:12px;letter-spacing:1.5px;display:flex;align-items:center;justify-content:center}

/* main */
.main{left:131px;top:338px;width:720px;height:698px;background:#fff}
.sidebar{left:139px;top:346px;width:155px;height:594px;background:var(--panel)}
.side-title{font-family:"Signika",sans-serif;font-weight:700;color:var(--blue);text-align:center;font-size:12.5px;line-height:1.1}
.wotd{left:146px;top:382px;width:138px;height:125px;background:#fff;text-align:center;padding-top:20px}
.wotd h3{font-family:"Signika",sans-serif;color:var(--orange);font-size:12.5px}
.wotd p{font-size:8px;color:var(--muted);line-height:13.5px;margin-top:9px;padding:0 14px}
.wotd .more{font-size:7.5px;font-weight:700;letter-spacing:1.2px;margin-top:11px;color:#444}
.ad-net{left:147px;top:518px;width:138px;height:114px;background:linear-gradient(135deg,#3a2c1e,#6b5536 55%,#2a2118)}
.ad-host{left:147px;top:765px;width:139px;height:115px;background:linear-gradient(160deg,#f6b73c,#e08a2a 60%,#2a6fb8)}
.email{left:149px;top:686px;width:135px;height:27px;background:#fff;border:1px solid #ccc;font-size:8px;color:#555;display:flex;align-items:center;padding-left:11px;gap:8px}
.signup{left:221px;top:718px;width:63px;height:22px;background:var(--orange);color:#fff;font-size:9px;font-weight:700;letter-spacing:1.3px;display:flex;align-items:center;justify-content:center}

.feature{left:302px;top:348px;width:541px;height:165px;border:1px solid var(--line);background:linear-gradient(#fff,#f5f5f5)}
.feature h2{position:absolute;left:21px;top:17px;font-family:"Signika",sans-serif;color:var(--blue);font-size:13.5px;letter-spacing:.2px}
.feature ul{position:absolute;left:26px;top:48px;list-style:none}
.feature li{font-size:8.5px;color:var(--muted);height:19.6px;display:flex;align-items:center;gap:11px}
.tick{width:8px;height:8px;border-radius:50%;background:var(--orange);display:inline-flex;align-items:center;justify-content:center}
.feature .art{position:absolute;right:23px;top:18px;width:198px;height:134px;border-radius:6px;background:radial-gradient(ellipse at 45% 60%,#f3dcb2,#ece7e0 70%,transparent)}

.promo{left:302px;top:524px;width:542px;height:67px;border:1px solid #222;background:#fff}
.promo .dot{position:absolute;left:16px;top:19px;width:30px;height:30px;border-radius:50%;background:#1d8fd2}
.promo p{position:absolute;left:58px;top:17px;font-family:"Signika",sans-serif;font-weight:700;font-size:12px;line-height:16px;color:#222}
.promo .cta{position:absolute;z-index:2;left:344px;top:22px;width:91px;height:23px;background:#d83a12;color:#fff;font-family:"Signika",sans-serif;font-weight:700;font-size:11px;display:flex;align-items:center;justify-content:center;white-space:nowrap}
.promo .shot{position:absolute;right:0;top:0;width:100px;height:65px;background:linear-gradient(120deg,#f4f4f4,#d6d6d6 45%,#2f3a3f)}

.card{width:267px;height:166px;border:1px solid var(--line);background:linear-gradient(#fff,#f4f4f4);text-align:center}
.card svg{margin-top:11px}
.card h3{font-family:"Signika",sans-serif;color:var(--blue);font-size:12.5px;margin-top:6px}
.card .tag{display:inline-block;margin-top:12px;border:1px solid #bbb;font-size:8.5px;padding:6px 14px;color:#333;background:#fff}
.card p{font-size:8.5px;color:var(--muted);line-height:14.5px;margin-top:8px;padding:0 38px}
.card p em{font-style:normal;color:var(--blue)}
.btn{display:inline-block;background:var(--orange-deep);color:#fff;font-size:8px;font-weight:700;letter-spacing:.4px;padding:4px 7px;margin-top:6px}

.browse{left:141px;top:964px;width:701px;height:63px;border:1px solid var(--line)}
.browse-label{left:420px;top:958px;background:#fff;padding:0 14px;font-size:9.5px;font-weight:700;color:#555;letter-spacing:.3px}
.letters{left:181px;top:985px;display:flex;gap:5.3px}
.letters span{width:18.4px;height:18.4px;border-radius:50%;border:1px solid #ccc;box-shadow:0 1px 2px rgba(0,0,0,.15);font-size:8.5px;color:#555;display:flex;align-items:center;justify-content:center;background:#fff}

/* footer */
.footer{left:0;top:1036px;width:982px;height:164px;background:var(--blue);color:#fff}
.fcol{position:absolute;top:24px}
.fcol h5{font-size:9.5px;font-weight:700;letter-spacing:.2px;margin-bottom:14px}
.fcol a{display:block;font-size:7.5px;color:#fff;text-decoration:none;line-height:15.3px}
.social{display:flex;gap:9px;margin-top:-2px}
.social i{width:20px;height:20px;border-radius:50%;display:block}
.fbrand{position:absolute;left:780px;top:26px;text-align:center;font-family:"Signika",sans-serif}
.fbrand b{display:block;font-size:20px;line-height:1}
.fbrand small{font-family:"Open Sans",sans-serif;font-size:9px;letter-spacing:.5px}
.frule{position:absolute;left:131px;top:121px;width:720px;border-top:1px solid rgba(255,255,255,.35)}
.copy{position:absolute;left:131px;top:139px;font-size:7.5px}
</style>
</head>
<body>

<header class="abs hero"></header>
<div class="abs menu"><span class="bars"></span>MENU</div>
<div class="abs brand"><b>Lumo</b><small>WORDFIND</small></div>
<div class="abs signin">SIGN IN</div>
<div class="abs join">JOIN FOR FREE</div>
<h1 class="abs hero-title">Lumo English Dictionary</h1>
<div class="abs search"><div class="field">Enter a Word or Phrase</div><div class="go">SEARCH</div></div>

<main class="abs main"></main>
<aside class="abs sidebar"></aside>
<div class="abs side-title" style="left:139px;top:359px;width:155px">WORD OF THE DAY</div>
<div class="abs wotd">
  <h3>EXHAUSTIVE</h3>
  <p>/ig-zaw-stiv/ (s) performed comprehensively and completely</p>
  <div class="more">READ MORE</div>
</div>
<div class="abs ad-net" role="img" aria-label="Advertisement: Corvanet networking, person holding a tablet at night"></div>
<div class="abs side-title" style="left:139px;top:651px;width:155px">SIGNUP FOR<br>NEWSLETTER</div>
<div class="abs email">
  <svg width="10" height="8" viewBox="0 0 10 8"><rect x=".5" y=".5" width="9" height="7" fill="none" stroke="#555"/><path d="M.5 .5 5 4.5 9.5 .5" fill="none" stroke="#555"/></svg>
  E mail id</div>
<div class="abs signup">SIGNUP</div>
<div class="abs ad-host" role="img" aria-label="Advertisement: NestHost web hosting with cartoon mascot"></div>

<section class="abs feature">
  <h2>SEARCH, SAVE AND MASTER WORDS</h2>
  <ul>
    <li><span class="tick"><svg width="6" height="5" viewBox="0 0 6 5"><path d="M.6 2.5 2.3 4 5.4 .8" fill="none" stroke="#fff" stroke-width="1.2"/></svg></span>Search from more than 300,000 words and phrases</li>
    <li><span class="tick"><svg width="6" height="5" viewBox="0 0 6 5"><path d="M.6 2.5 2.3 4 5.4 .8" fill="none" stroke="#fff" stroke-width="1.2"/></svg></span>Multiple usages to clarify the context</li>
    <li><span class="tick"><svg width="6" height="5" viewBox="0 0 6 5"><path d="M.6 2.5 2.3 4 5.4 .8" fill="none" stroke="#fff" stroke-width="1.2"/></svg></span>Audio, phonetics, meanings, synonyms and antonyms</li>
    <li><span class="tick"><svg width="6" height="5" viewBox="0 0 6 5"><path d="M.6 2.5 2.3 4 5.4 .8" fill="none" stroke="#fff" stroke-width="1.2"/></svg></span>Save the words to your personal deck and access from anywhere</li>
    <li><span class="tick"><svg width="6" height="5" viewBox="0 0 6 5"><path d="M.6 2.5 2.3 4 5.4 .8" fill="none" stroke="#fff" stroke-width="1.2"/></svg></span>It's FREE</li>
  </ul>
  <div class="art" role="img" aria-label="Illustration of a boy with a magnifying glass beside an open alphabet book"></div>
</section>

<section class="abs promo">
  <span class="dot"></span>
  <p>53% of IT managers said printers were vulnerable<br>to cyber crime. What defense do you have?</p>
  <span class="cta">Find out more</span>
  <div class="shot" role="img" aria-label="Pendra office printer and monitor"></div>
</section>

<div class="abs card" style="left:302px;top:602px">
  <svg width="30" height="22" viewBox="0 0 30 22"><path d="M3 18 9 2h2l6 16M5.5 12h9" fill="none" stroke="#666" stroke-width="1.6"/><path d="M0 9h30" stroke="#666" stroke-width="1.2"/><text x="20" y="21" font-size="11" font-family="Open Sans" fill="#666">b</text></svg>
  <h3>ENGLISH TIDBIT</h3>
  <span class="tag">gaffe/gaff</span>
  <p><em>"Gaffe"</em> is a social blunder and <em>"gaff"</em> is a large hook. Be warned not to make the gaffe of mixing it up with gaff.</p>
</div>
<div class="abs card" style="left:578px;top:602px">
  <svg width="24" height="24" viewBox="0 0 24 24"><rect x="1" y="1" width="22" height="22" fill="none" stroke="#777" stroke-width="1.2"/><path d="M8.3 1v22M15.6 1v22M1 8.3h22M1 15.6h22" stroke="#777"/><rect x="1" y="1" width="7.3" height="7.3" fill="#888"/><rect x="15.6" y="8.3" width="7.3" height="7.3" fill="#888"/><rect x="8.3" y="15.6" width="7.3" height="7.3" fill="#888"/></svg>
  <h3>DAILY CROSSWORD</h3>
  <span class="tag">Crossword Lovers!</span>
  <p>Take this daily crossword challenge from Lumo Wordfind.</p>
  <span class="btn">SOLVE NOW</span>
</div>
<div class="abs card" style="left:302px;top:776px">
  <svg width="30" height="34" viewBox="0 0 30 34"><circle cx="15" cy="20" r="12" fill="none" stroke="#777" stroke-width="3"/><path d="M15 2v10M10 7h10" stroke="#777" stroke-width="1.6"/></svg>
  <h3>FOXTAIL ADDON</h3>
  <p>Add this tool to your Foxtail browser and quickly look up for definitions from any website without leaving the page.</p>
  <span class="btn" style="margin-top:10px">GET IT NOW</span>
</div>
<div class="abs card" style="left:578px;top:776px">
  <svg width="18" height="34" viewBox="0 0 18 34"><rect x="1.5" y="1.5" width="15" height="31" rx="2.5" fill="none" stroke="#777" stroke-width="1.8"/><path d="M1.5 6h15M1.5 27h15" stroke="#777"/><circle cx="9" cy="30" r="1.3" fill="#777"/></svg>
  <h3>DESIGNED FOR KIVO PHONE</h3>
  <p>Lumo Wordfind is specially designed for your Kivo phone to quickly lookup meaining, usages and audio of words.</p>
  <span class="btn" style="margin-top:10px">GET IT NOW</span>
</div>

<div class="abs browse"></div>
<div class="abs browse-label">BROWSE DICTIONARY</div>
<div class="abs letters">
  <span>A</span><span>B</span><span>C</span><span>D</span><span>E</span><span>F</span><span>G</span><span>H</span><span>I</span><span>J</span><span>K</span><span>L</span><span>M</span><span>N</span><span>O</span><span>P</span><span>Q</span><span>R</span><span>S</span><span>T</span><span>U</span><span>V</span><span>W</span><span>X</span><span>Y</span><span>Z</span>
</div>

<footer class="abs footer">
  <div class="fcol" style="left:131px"><h5>LUMOWORDFIND.COM</h5><a>FAQ</a><a>Contact</a><a>Blog</a></div>
  <div class="fcol" style="left:315px"><h5>LEGAL</h5><a>Privacy Policy</a><a>Terms of Use</a></div>
  <div class="fcol" style="left:455px"><h5>OTHERS</h5><a>Popular Words</a><a>Common Errors in English</a><a>Exam Prep Online</a></div>
  <div class="fcol" style="left:623px"><h5>FOLLOW US ON</h5>
    <div class="social"><i style="background:#1f4f9a"></i><i style="background:#1da1f2"></i><i style="background:#d4202a"></i><i style="background:#1f6aa8"></i></div>
  </div>
  <div class="fbrand"><b>Lumo</b><small>WORDFIND</small></div>
  <div class="frule"></div>
  <div class="copy">Copyrights @ 2016 All Rights Reserved</div>
</footer>

</body>
</html>
```